Health Supplement Series for 60 tablets of pure Amber Vine Core powder

We need a packaging design theme for a health supplement for international consumers. Our initial product is called 'Amber Vine Core'. It is for general health and is particularly effective for diabetic symptoms.
We would like to see designs that are clean and fresh.
It should give the impression of professional, premium pharmaceutical grade products.
Our company logo is attached below.

Target Market(s)

International

Industry/Entity Type

Health And Wellness

Font styles to use
Serif
Sans Serif

Requirements
Must have
• Bottle and box packaging required.
• 1st product is bottle of 60 tablets of 0.5gm each.
Should not have
• Seals and other "must buy" "guaranteed" etc

```html
<!DOCTYPE html>
<html lang="en">
<head>
<meta charset="utf-8">
<title>Amber Vine Core – Bottle Label</title>
<link rel="stylesheet" href="https://fonts.googleapis.com/css2?family=Open+Sans:wght@400;600;700&display=swap">
<style>
  :root {
    --backdrop: #ececec;
    --label-white: #ffffff;
    --band-brown: #4a200f;
    --title-brown: #5a2a14;
    --ribbon-dark: #5b2410;
    --ribbon-tan: #c89462;
    --brand-green: #5a9a2a;
    --body-grey: #444444;
  }
  * { margin: 0; padding: 0; box-sizing: border-box; }
  html, body {
    width: 1158px;
    height: 1200px;
    overflow: hidden;
    background: var(--backdrop);
    font-family: "Open Sans", Arial, sans-serif;
  }
  .label {
    position: absolute;
    left: 139px;
    top: 58px;
    width: 880px;
    height: 1083px;
    background: var(--label-white);
    overflow: hidden;
  }
  .label-band {
    position: absolute;
    left: 0;
    width: 100%;
    height: 18px;
    background: var(--band-brown);
  }
  .label-band--top { top: 0; }
  .label-band--bottom { bottom: 0; }

  .brand {
    position: absolute;
    left: 108px;
    top: 128px;
    display: flex;
    align-items: center;
    gap: 8px;
    color: var(--brand-green);
    font-weight: 600;
  }
  .brand-square {
    width: 40px;
    height: 52px;
    background: var(--brand-green);
  }
  .brand-name { line-height: 1; }
  .brand-name-main { display: block; font-size: 38px; letter-spacing: 3px; }
  .brand-name-sub { display: block; font-size: 15px; margin-top: 4px; }

  .product-title {
    position: absolute;
    left: 95px;
    top: 205px;
    color: var(--title-brown);
    font-weight: 700;
    font-size: 126px;
    line-height: 124px;
    letter-spacing: -2px;
  }
  .product-title span { display: block; }

  .product-copy {
    position: absolute;
    left: 100px;
    top: 608px;
    width: 330px;
    color: var(--body-grey);
    font-size: 21px;
    line-height: 28px;
  }

  .vine-art {
    position: absolute;
    left: 630px;
    top: 0;
    width: 210px;
    height: 660px;
    background: linear-gradient(180deg, rgba(200,148,98,0.55), rgba(122,62,28,0.45) 60%, rgba(90,36,16,0.25));
    border-radius: 0 0 100px 100px;
  }

  .ribbon {
    position: absolute;
    left: 0;
    top: 0;
    width: 880px;
    height: 1083px;
  }

  .seed-photo {
    position: absolute;
    left: 352px;
    top: 627px;
    width: 517px;
    height: 435px;
    border-radius: 46% 46% 40% 40%;
    background: radial-gradient(ellipse at 50% 50%, #b5683a 0%, #8a4524 45%, #5b2a14 75%, rgba(91,42,20,0) 100%);
  }
</style>
</head>
<body>
  <main class="label">
    <div class="label-band label-band--top"></div>

    <div class="vine-art" role="img" aria-label="Decorative climbing vine with brown and tan leaves"></div>

    <div class="brand">
      <div class="brand-square"></div>
      <div class="brand-name">
        <span class="brand-name-main">CALDER</span>
        <span class="brand-name-sub">BIOTECH LIMITED</span>
      </div>
    </div>

    <h1 class="product-title">
      <span>AMBER</span>
      <span>VINE</span>
      <span>CORE</span>
    </h1>

    <p class="product-copy">Lorem ipsum dolor sit amet, consectetur adipiscing elit. Ut mollis lobortis tempus. Donec</p>

    <svg class="ribbon" viewBox="0 0 880 1083" aria-hidden="true">
      <path d="M0 945 C120 880 240 860 360 900 C450 930 520 990 600 1040 L600 1065 C520 1020 440 960 360 935 C240 900 120 920 0 985 Z" fill="var(--ribbon-tan)"/>
      <path d="M0 860 C90 830 170 840 250 880 C340 925 430 1000 520 1045 L490 1065 C400 1020 320 960 240 920 C160 880 80 875 0 900 Z" fill="var(--ribbon-dark)"/>
    </svg>

    <div class="seed-photo" role="img" aria-label="Photograph of cracked brown vine seeds and shells"></div>

    <div class="label-band label-band--bottom"></div>
  </main>
</body>
</html>
```